1/4 page ad for Brightmoor magazine

Placing an ad in the Brightmoor Canada magazine.
3.475 (w) x 4.75 (h)
Please design in Adobe Illustrator and provide original file.
Logo attached.
Prior brochure attached.
Please include website and contact info.

```html
<!DOCTYPE html>
<html lang="en">
<head>
<meta charset="utf-8">
<title>Aquavera – Quarter Page Ad</title>
<link href="https://fonts.googleapis.com/css2?family=Montserrat:wght@500;600;700;800;900&display=swap" rel="stylesheet">
<style>
  :root {
    --green-dark: #2f7f34;
    --green: #3b9440;
    --green-mid: #4fa646;
    --green-light: #6cbf3f;
    --mint: #e4f1e2;
    --mint-pale: #f3f8f1;
    --ink: #1d1d1b;
    --white: #ffffff;
    --stage: #d9d9d9;
  }
  html, body {
    margin: 0;
    padding: 0;
    width: 967px;
    height: 1200px;
    overflow: hidden;
    background: var(--stage);
    font-family: "Montserrat", Arial, sans-serif;
  }
  .ad {
    position: absolute;
    left: 53px;
    top: 12px;
    width: 860px;
    height: 1176px;
    overflow: hidden;
    background: linear-gradient(160deg, var(--mint) 0%, var(--mint-pale) 55%, #eef5ec 100%);
    box-shadow: 0 2px 6px rgba(0,0,0,.25);
  }
  .ad-shapes { position: absolute; inset: 0; }
  .droplets {
    position: absolute;
    right: 0; top: 0;
    width: 460px; height: 230px;
    background: radial-gradient(ellipse at 75% 30%, #ffffff 0%, #dfe8df 45%, rgba(228,241,226,0) 75%);
  }
  .leaves {
    position: absolute;
    right: 0; top: 370px;
    width: 90px; height: 150px;
    border-radius: 70% 0 0 70%;
    background: radial-gradient(ellipse at 70% 50%, var(--green-light) 0%, #8fd14f 45%, rgba(143,209,79,0) 78%);
  }
  .brand {
    position: absolute;
    left: 44px; top: 26px;
  }
  .brand-square {
    display: block;
    width: 72px; height: 72px;
    margin-bottom: 12px;
    background: var(--white);
    border-radius: 10px;
  }
  .brand-name {
    font-size: 32px;
    font-weight: 700;
    color: var(--white);
    line-height: 1;
  }
  .headline {
    position: absolute;
    left: 0; top: 232px;
    width: 860px;
    margin: 0;
    text-align: center;
    font-weight: 900;
    font-size: 48px;
    line-height: 57px;
    letter-spacing: 1px;
    color: var(--green-dark);
    text-transform: uppercase;
  }
  .headline .sub {
    display: block;
    color: var(--green-mid);
    font-size: 42px;
    line-height: 56px;
  }
  .divider {
    position: absolute;
    left: 355px; top: 500px;
    width: 150px; height: 4px;
    background: var(--green-dark);
  }
  .product-photo {
    position: absolute;
    left: 40px; top: 540px;
    width: 300px; height: 600px;
    background: linear-gradient(160deg, #f2f2f2 0%, #d7d9d8 55%, #a9c9a6 100%);
    clip-path: polygon(6% 5%, 52% 0, 70% 3%, 70% 62%, 100% 72%, 100% 90%, 22% 100%, 6% 96%);
  }
  .features {
    position: absolute;
    left: 360px; top: 548px;
    margin: 0; padding: 0;
    list-style: none;
    width: 460px;
  }
  .features li {
    position: relative;
    padding-left: 38px;
    font-size: 20px;
    font-weight: 600;
    line-height: 27px;
    color: var(--ink);
    margin-bottom: 24px;
  }
  .features li::before {
    content: "";
    position: absolute;
    left: 0; top: 3px;
    width: 22px; height: 22px;
    border-radius: 4px;
    background: var(--green);
  }
  .contact {
    position: absolute;
    left: 336px; top: 1030px;
    color: var(--white);
  }
  .contact-call { font-size: 20px; font-weight: 700; }
  .contact-phone {
    display: flex; align-items: center; gap: 8px;
    font-size: 46px; font-weight: 800; line-height: 58px; letter-spacing: .5px;
  }
  .contact-web { font-size: 14px; font-weight: 500; }
</style>
</head>
<body>
  <div class="ad">
    <svg class="ad-shapes" width="860" height="1176" viewBox="0 0 860 1176" aria-hidden="true">
      <rect x="0" y="0" width="34" height="1176" fill="#2f7f34"/>
      <path d="M0 0 H300 V90 A120 120 0 0 1 180 210 H0 Z" fill="#3b9440"/>
      <path d="M0 0 H190 C120 20 70 90 60 210 H0 Z" fill="#2f7f34"/>
      <path d="M210 1176 V1090 C210 1060 228 1042 256 1042 H280 C306 1042 320 1060 320 1088 V1176 Z" fill="#4fa646" opacity=".8"/>
      <path d="M310 1176 V1050 C310 1025 326 1010 352 1010 H860 V1176 Z" fill="#3b9440"/>
      <path d="M352 1010 H860 V1040 C720 1020 540 1035 352 1050 Z" fill="#4fa646" opacity=".5"/>
    </svg>
    <div class="droplets" role="img" aria-label="Water droplets on a glass surface"></div>
    <div class="leaves" role="img" aria-label="Fresh green leaves with a water drop"></div>

    <div class="brand">
      <span class="brand-square"></span>
      <div class="brand-name">aquavera</div>
    </div>

    <h1 class="headline">Disinfection,<br>Decontamination,<br>and Aeration<span class="sub">All in one product</span></h1>
    <div class="divider"></div>

    <div class="product-photo" role="img" aria-label="Ozone water treatment unit with control panel, piping and bubble molecules"></div>

    <ul class="features">
      <li>Faster and more effective than alternatives (e.g. chlorine, UV, RO etc.)</li>
      <li>No chemicals added or left behind</li>
      <li>Supersaturates water with oxygen</li>
      <li>Ideal for treating recirculated water, reservoirs, irrigation lines, drains, and sumps</li>
    </ul>

    <div class="contact">
      <div class="contact-call">Call Us Anytime!</div>
      <div class="contact-phone">
        <svg width="36" height="36" viewBox="0 0 34 34" aria-hidden="true">
          <circle cx="17" cy="17" r="16" fill="#ffffff"/>
          <path d="M11 9 l4 0 l1.5 5 -2.5 2 c1 2.5 2.5 4 5 5 l2 -2.5 5 1.5 0 4 c-9 1 -16 -6 -15 -15z" fill="#3b9440"/>
        </svg>
        1-888-555-0147
      </div>
      <div class="contact-web">● www.aquavera-water.com &nbsp;|&nbsp; ● info@aquavera-water.com</div>
    </div>
  </div>
</body>
</html>
```